Postcard design to acquire new clients for my Property Management Company

I'm looking for a postcard design that I can send to prospective clients detailing information about my company and services.
Postcard should be eye catching and contain information from www.bramblecrestpm.com. I've provided a few screen shots for the most important information and my logo.
Target Market(s)
Real Estate
Industry/Entity Type
Real Estate
Font styles to use
Sans Serif
Requirements
Must have
- Must be eye catching!! this will be a direct mail piece - I'd like for the card to be read and not tossed in the trash immediately.
Design que from the logo.
A place to write / print the receipts name and address.
our physical address - 2387 Hollow Pine Road, Lubbock, TX 79852.
Should not have
- the contact information on the business card is not accurate - please use info from website.

```html
<!DOCTYPE html>
<html lang="en">
<head>
<meta charset="UTF-8">
<title>Bramblecrest Property Management – Postcard</title>
<link href="https://fonts.googleapis.com/css2?family=Montserrat:wght@300;400;500;600;700;800&display=swap" rel="stylesheet">
<style>
  :root{
    --navy:#0f4a85;
    --navy-deep:#163a78;
    --navy-band:#2e4f8f;
    --blue:#1a52a0;
    --ink:#0f4a85;
    --grey-text:#6d6f72;
    --grey-stripe:#a6a8ab;
    --panel:#eeeff0;
    --panel-light:#f7f7f8;
    --white:#ffffff;
    --rule:#b9bcc0;
  }
  *{box-sizing:border-box;margin:0;padding:0}
  html,body{width:995px;height:1200px;overflow:hidden}
  body{background:var(--navy);font-family:"Montserrat",Arial,sans-serif;position:relative}
  .card{position:absolute;left:67px;width:860px;height:570px;overflow:hidden;background:var(--panel);box-shadow:0 4px 14px rgba(0,0,0,.25)}
  .card--front{top:20px}
  .card--back{top:610px}
  .card__shapes{position:absolute;inset:0;width:100%;height:100%}
  .abs{position:absolute}

  /* brand */
  .brand__name{font-weight:700;color:var(--ink);letter-spacing:.12em;line-height:1}
  .brand__tag{font-weight:400;color:var(--ink);letter-spacing:.2em;line-height:1}
  .front .brand{left:49px;top:62px}
  .front .brand__name{font-size:38px}
  .front .brand__tag{font-size:18px;margin-top:8px;letter-spacing:.21em}

  .front__headline{left:50px;top:196px;font-size:25px;font-weight:800;color:var(--ink);line-height:1.35}
  .front__lede{left:50px;top:292px;font-size:19px;font-weight:300;color:var(--grey-text);line-height:1.3;width:260px}
  .front__contact{left:49px;top:416px}
  .contact__title{font-size:23px;font-weight:800;color:var(--ink)}
  .contact__label{font-size:15px;font-weight:300;color:var(--grey-text);margin-top:12px}
  .contact__phone{font-size:20px;font-weight:700;color:var(--ink)}
  .contact__email{font-size:16px;font-weight:300;color:var(--grey-text)}

  /* back */
  .back__headline{left:41px;top:40px;font-size:25px;font-weight:800;color:var(--ink);line-height:1.3}
  .back__lede{left:41px;top:118px;font-size:16px;font-weight:400;color:var(--grey-text);line-height:1.3;width:260px}
  .services{left:28px;top:176px;display:grid;grid-template-columns:repeat(4,98px);row-gap:14px}
  .service{text-align:center;font-size:12.5px;color:var(--grey-text);line-height:1.2}
  .service svg{display:block;margin:0 auto 4px;height:22px;width:24px}
  .service svg *{fill:var(--navy)}
  .back .brand{left:488px;top:30px}
  .back .brand__name{font-size:23px;letter-spacing:.1em}
  .back .brand__tag{font-size:11.5px;margin-top:4px;letter-spacing:.17em}

  .choose{left:40px;top:375px;font-size:16px;font-weight:800;color:var(--white);line-height:1.3}
  .back__contact{left:40px;top:508px;width:155px;color:var(--white);line-height:1.2}
  .back__contact .l{font-size:11px;font-weight:300}
  .back__contact .p{font-size:13.5px;font-weight:700}
  .back__contact .e{font-size:10.5px;font-weight:300;white-space:nowrap}

  .plan{position:absolute;background:var(--white);text-align:center;padding:10px 4px;box-shadow:0 2px 6px rgba(0,0,0,.25)}
  .plan__name{font-size:10.5px;font-weight:800;color:var(--ink)}
  .plan__note{font-size:6.5px;color:var(--grey-text);margin-top:1px}
  .plan__rate{font-size:17px;font-weight:800;color:var(--ink);margin-top:6px}
  .plan__basis{font-size:6px;color:var(--grey-text);margin-bottom:8px}
  .plan li{list-style:none;font-size:6px;color:var(--grey-text);margin-bottom:8px}
  .plan--lease{left:205px;top:363px;width:114px;height:190px}
  .plan--full{left:326px;top:357px;width:116px;height:207px}
  .plan--premium{left:449px;top:363px;width:116px;height:136px}

  /* mailing panel */
  .mailing{left:622px;top:404px;width:222px;height:150px;background:var(--white);padding:10px 12px;box-shadow:0 2px 6px rgba(0,0,0,.25)}
  .mailing__return{font-size:8px;line-height:1.35;color:var(--grey-text)}
  .mailing__return strong{color:var(--ink);font-weight:700}
  .mailing__label{font-size:7px;font-weight:600;color:var(--ink);letter-spacing:.1em;margin-top:14px}
  .mailing__line{height:16px;border-bottom:1px solid var(--rule)}
</style>
</head>
<body>

<!-- FRONT -->
<section class="card card--front front">
  <svg class="card__shapes" viewBox="0 0 740 490" preserveAspectRatio="none">
    <defs>
      <linearGradient id="keyPhoto" x1="0" y1="0" x2="1" y2="1">
        <stop offset="0" stop-color="#8d8a86"/>
        <stop offset=".5" stop-color="#4c5a60"/>
        <stop offset="1" stop-color="#7a7772"/>
      </linearGradient>
    </defs>
    <rect width="740" height="490" fill="var(--panel)"/>
    <polygon points="0,0 300,0 120,490 0,490" fill="var(--panel-light)" opacity=".6"/>
    <polygon points="300,300 340,300 265,490 225,490" fill="var(--grey-stripe)"/>
    <polygon points="495,0 740,0 740,490 300,490" fill="var(--blue)"/>
    <g role="img" aria-label="Photo: person in a striped sweater handing over a house key">
      <polygon points="530,0 740,0 740,490 330,490" fill="url(#keyPhoto)"/>
    </g>
    <polygon points="330,490 740,490 740,480 334,480" fill="var(--navy-deep)"/>
  </svg>

  <div class="abs brand">
    <div class="brand__name">BRAMBLECREST</div>
    <div class="brand__tag">PROPERTY MANAGEMENT</div>
  </div>
  <h1 class="abs front__headline">PROPERTY MANAGEMENT<br>ACROSS LUBBOCK, TX</h1>
  <p class="abs front__lede">Maximize your financial returns with support from our rental specialists</p>
  <div class="abs front__contact">
    <div class="contact__title">Contact Our Team</div>
    <div class="contact__label">Call Now:</div>
    <div class="contact__phone">(806) 555-0148</div>
    <div class="contact__email">info@bramblecrestpm.com</div>
  </div>
</section>

<!-- BACK -->
<section class="card card--back back">
  <svg class="card__shapes" viewBox="0 0 740 490" preserveAspectRatio="none">
    <defs>
      <linearGradient id="officePhoto" x1="0" y1="0" x2="1" y2="1">
        <stop offset="0" stop-color="#c9d3dc"/>
        <stop offset=".55" stop-color="#5d7590"/>
        <stop offset="1" stop-color="#9a8f80"/>
      </linearGradient>
    </defs>
    <rect width="740" height="490" fill="var(--panel)"/>
    <g role="img" aria-label="Photo: two smiling professionals reviewing documents in an office with a city view">
      <polygon points="380,0 740,0 740,490 470,490 470,292" fill="url(#officePhoto)"/>
    </g>
    <polygon points="310,0 345,0 430,205 395,205" fill="var(--grey-stripe)"/>
    <polygon points="355,0 380,0 480,292 452,292" fill="var(--blue)"/>
    <polygon points="415,0 740,0 740,60 445,60" fill="var(--white)" opacity=".55"/>
    <rect x="0" y="292" width="470" height="198" fill="var(--navy-band)"/>
  </svg>

  <div class="abs brand">
    <div class="brand__name">BRAMBLECREST</div>
    <div class="brand__tag">PROPERTY MANAGEMENT</div>
  </div>

  <h2 class="abs back__headline">DISCOVER OUR<br>SERVICES</h2>
  <p class="abs back__lede">We offer full-service property management solutions</p>

  <div class="abs services">
    <div class="service"><svg viewBox="0 0 24 22"><path d="M12 2 1 11h3v9h6v-6h4v6h6v-9h3z"/></svg>Property<br>Marketing</div>
    <div class="service"><svg viewBox="0 0 24 22"><circle cx="8" cy="7" r="4"/><circle cx="17" cy="7" r="4"/><path d="M0 19c0-5 4-7 8-7s8 2 8 7z"/><path d="M10 19c0-5 3-7 7-7s7 2 7 7z"/></svg>Tenant<br>Screening</div>
    <div class="service"><svg viewBox="0 0 24 22"><text x="12" y="20" text-anchor="middle" font-size="22" font-weight="800" font-family="Montserrat,sans-serif">$</text></svg>Rent<br>Collection</div>
    <div class="service"><svg viewBox="0 0 24 22"><rect x="11" y="2" width="2" height="16"/><rect x="3" y="4" width="18" height="2"/><rect x="7" y="18" width="10" height="2"/><path d="M0 13h10l-5-8zM14 13h10l-5-8z"/></svg>Legal<br>Guidance</div>
    <div class="service"><svg viewBox="0 0 24 22"><path d="M9 2h8l3 3v3h-3l-2-2h-6z"/><rect x="10" y="7" width="3.5" height="15" transform="rotate(35 12 14)"/></svg>Maintenance</div>
    <div class="service"><svg viewBox="0 0 24 22"><path d="M10 2a7 7 0 1 0 0 14 7 7 0 0 0 0-14zm0 3a4 4 0 1 1 0 8 4 4 0 0 1 0-8z"/><rect x="15" y="13" width="3" height="9" transform="rotate(-45 16 17)"/></svg>Property<br>Inspections</div>
    <div class="service"><svg viewBox="0 0 24 22"><rect x="2" y="18" width="20" height="2"/><rect x="2" y="4" width="2" height="14"/><rect x="7" y="10" width="2" height="7"/><rect x="11" y="7" width="2" height="10"/><rect x="15" y="11" width="2" height="6"/><rect x="19" y="5" width="2" height="12"/></svg>Financial<br>Reporting</div>
    <div class="service"><svg viewBox="0 0 24 22"><path d="M12 1 3 4v7c0 5 4 9 9 10 5-1 9-5 9-10V4z"/></svg>Evictions</div>
  </div>

  <h3 class="abs choose">CHOOSE<br>THE RIGHT<br>PROPERTY<br>MANAGEMENT<br>SYSTEM</h3>
  <div class="abs back__contact">
    <div class="l">Call Now:</div>
    <div class="p">(806) 555-0148</div>
    <div class="e">info@bramblecrestpm.com</div>
  </div>

  <div class="plan plan--lease">
    <div class="plan__name">Lease Only</div>
    <div class="plan__note">- You Just Need Tenants -</div>
    <div class="plan__rate">9%</div>
    <div class="plan__basis">of annual lease</div>
    <ul>
      <li>Professional Photography</li>
      <li>Marketing &amp; Advertising</li>
      <li>Property Showings</li>
      <li>Tenant Screening &amp; Qualifications</li>
      <li>Lease Execution</li>
      <li>Move In Coordination</li>
    </ul>
  </div>
  <div class="plan plan--full">
    <div class="plan__name">Full Service</div>
    <div class="plan__note">- Our Most Popular -</div>
    <div class="plan__rate">10%</div>
    <div class="plan__basis">of monthly rent</div>
    <ul>
      <li>Includes Leasing Service</li>
      <li>24/7 Emergency Response</li>
      <li>Move In &amp; Out Inspections</li>
      <li>Professional Lease Enforcement</li>
      <li>Schedule &amp; Oversee all Repairs</li>
      <li>Pay all Invoices</li>
      <li>Monthly &amp; Year End Statements</li>
      <li>Annual Market Rent Analysis</li>
    </ul>
  </div>
  <div class="plan plan--premium">
    <div class="plan__name">Premium Service</div>
    <div class="plan__note">- Our Premier Service -</div>
    <div class="plan__rate">12%</div>
    <div class="plan__basis">of monthly rent</div>
    <ul>
      <li>Includes Full Service Features</li>
      <li>Professional Video Marketing</li>
      <li>Home Warranty Coordination</li>
      <li>Tenant Retention Program</li>
    </ul>
  </div>

  <div class="abs mailing">
    <p class="mailing__return"><strong>Bramblecrest Property Management</strong><br>2387 Hollow Pine Road<br>Lubbock, TX 79852</p>
    <div class="mailing__label">MAIL TO:</div>
    <div class="mailing__line"></div>
    <div class="mailing__line"></div>
    <div class="mailing__line"></div>
  </div>
</section>

</body>
</html>
```